KRV Business Card

Looking for a business card for my restaurant group I own. Four different concepts:

Copperfield Alehouse
Bristow Alehouse
Tanager's Stone Hearth Kitchen
Pellston Patty Company

Card doesn't need to include all the logos.

```html
<!DOCTYPE html>
<html lang="en">
<head>
<meta charset="utf-8">
<title>KRV Business Card</title>
<link rel="stylesheet" href="https://fonts.googleapis.com/css2?family=Josefin+Sans:wght@600&family=Lato:wght@400;700&display=swap">
<style>
  :root {
    --bg: #e3e3e3;
    --gold: #d4b06b;
    --gold-text: #c9a55c;
    --white: #ffffff;
    --ink: #2b2b2b;
    --display: "Josefin Sans", sans-serif;
    --body: "Lato", sans-serif;
  }
  * { margin: 0; padding: 0; box-sizing: border-box; }
  html, body { width: 1200px; height: 900px; overflow: hidden; }
  body { background: var(--bg); position: relative; font-family: var(--body); }

  .card {
    position: absolute;
    width: 520px;
    height: 300px;
    border-radius: 26px;
    overflow: hidden;
  }

  /* Back: gold */
  .card-back {
    left: 110px; top: 120px;
    background: var(--gold);
    color: var(--white);
    display: flex; flex-direction: column; align-items: center; justify-content: center;
    text-align: center;
  }
  .brand-name {
    font-family: var(--display);
    font-weight: 600;
    text-transform: uppercase;
    line-height: 1.1;
  }
  .card-back .brand-name { font-size: 34px; letter-spacing: 5px; }
  .card-back .brand-name span { display: block; font-size: 17px; letter-spacing: 4px; margin-top: 6px; }
  .rule { width: 320px; height: 1px; background: var(--white); margin: 16px 0 10px; }
  .concepts {
    font-size: 12.5px;
    letter-spacing: 0.6px;
    text-transform: uppercase;
    line-height: 1.45;
  }

  /* Front: white */
  .card-front {
    left: 570px; top: 480px;
    background: var(--white);
    color: var(--ink);
  }
  .card-front .brand-name {
    position: absolute;
    left: 34px; top: 58px;
    color: var(--gold-text);
    font-size: 25px;
    letter-spacing: 4px;
  }
  .card-front .brand-name span { display: block; font-size: 14px; letter-spacing: 3px; margin-top: 4px; }
  .person { position: absolute; left: 34px; top: 132px; }
  .person-name { font-weight: 700; font-size: 18px; letter-spacing: 1px; color: var(--gold-text); text-transform: uppercase; }
  .person-role { font-size: 14px; margin-top: 2px; }
  .contacts { list-style: none; margin-top: 12px; }
  .contacts li { display: flex; align-items: center; gap: 8px; font-size: 14.5px; line-height: 1.5; }
  .contacts svg { width: 12px; height: 12px; flex: none; }
  .address {
    position: absolute;
    right: 30px; top: 92px;
    font-size: 13.5px; line-height: 1.45;
    text-align: left;
  }
</style>
</head>
<body>

<section class="card card-back">
  <h1 class="brand-name">Kestrel Ridge<span>Hospitality Group</span></h1>
  <div class="rule"></div>
  <p class="concepts">Copperfield Alehouse | Bristow Alehouse<br>Tanager's Stone Hearth Kitchen | Pellston Patty Company</p>
</section>

<section class="card card-front">
  <h2 class="brand-name">Kestrel Ridge<span>Hospitality Group</span></h2>
  <div class="person">
    <p class="person-name">Daniel Harrow</p>
    <p class="person-role">Managing Director</p>
    <ul class="contacts">
      <li>
        <svg viewBox="0 0 12 12" aria-hidden="true"><path fill="#c9a55c" d="M2 1h2.5l1 2.5-1.5 1a6 6 0 0 0 3.5 3.5l1-1.5 2.5 1V10a1 1 0 0 1-1 1A9 9 0 0 1 1 2a1 1 0 0 1 1-1z"/></svg>
        044-987 650 312
      </li>
      <li>
        <svg viewBox="0 0 12 12" aria-hidden="true"><rect x="0.5" y="2" width="11" height="8" rx="1" fill="#c9a55c"/><path d="M1 2.5l5 4 5-4" stroke="#fff" stroke-width="1" fill="none"/></svg>
        hello@krvgroup.com
      </li>
      <li>
        <svg viewBox="0 0 12 12" aria-hidden="true"><circle cx="6" cy="6" r="5.5" fill="#c9a55c"/><path d="M0.5 6h11M6 0.5c-3 3-3 8 0 11M6 0.5c3 3 3 8 0 11" stroke="#fff" stroke-width="0.8" fill="none"/></svg>
        www.krvgroup.com
      </li>
    </ul>
  </div>
  <p class="address">88, Harbor Lane West<br>Westfield County, 45190</p>
</section>

</body>
</html>
```